Backdrop Banner to be designed for a kids handwriting company

We are an occupational therapy company that helps children improve their handwriting. We give online lessons and make how-to videos for the kids to watch. We are looking for a backdrop to be designed that can be placed on a roller blind to use when needed. Size to be 183cm (width) x200cm (height). The final design needs to be produced in a format that can be uploaded to a printing company for them to produce.

We need our logo to be displayed. Our corporate colours are: #ff0069, #2abeb0, #ffc700, #93db40, #322e58. If you wish to see our current 'look' go to www.penpathlearning.co.uk. We can tell you our fonts if asked.

We work with children aged 6 to 16 years, mainly 10 to 13 years. In the past, I have placed motivational stickers on the back of my wall. Many of the children we see have lost confidence in themselves hence the words 'Believe in yourself', 'Make it happen' etc. were chosen. We teach them how to write clearly so the teachers can read/mark their work, parents are happy and we boost their self confidence. We are open to positive words or doodle style images but they cannot be cutesy. The backdrop must not overpower a lesson and take away the kid's focus.

I have included some ideas, our logo and a picture of what is the backdrop in my office.
1. We are open to keeping everything in the right-hand corner of the screen so the kids see us and any image is to the right (as per the picture). If doing this the images will need to sit from 30cm to 80cm from the top of the blind when fully down. Width needed is probably 65cm.
2. We are open to the parkour concept of words and images going across the whole backdrop or on the right hand side.
3. We are open to the backdrop having one image on its own whether that be random or specific images.
4. If using any writing the font has to be readable, no imitation of 'bad' handwriting. We see kids at any time of the day so we cannot have it say 'Good morning'.

We are hoping you will be inspired by this project as we'd love to work with you and see your ideas.

UPDATE 1 - 03.08.23: Based on the designs submitted so far please watch the wording of any motivational words and keep in mind this is a backdrop banner only the top half is likely to be seen on screen and there will be a person sitting in front of your design.

UPDATE 2 - 04.08.23: Mock up images with measurements added to help you design this backdrop for a video.

UPDATE: Based on the designs submitted so far please watch the wording of any motivational words and keep in mind this is a backdrop banner only the top half is likely to be seen on screen and there will be a person sitting in front of your design.

Supplied this in the brief

Other font styles liked:
• Business fonts on website are Kind Heart, Logo is Typo Round Regular

• Supplied this in the brief

```html
<!DOCTYPE html>
<html lang="en">
<head>
<meta charset="utf-8">
<title>Believe in Yourself – Pen Path Learning Backdrop</title>
<link href="https://fonts.googleapis.com/css2?family=Luckiest+Guy&family=Fredoka:wght@500;600;700&display=swap" rel="stylesheet">
<style>
  :root {
    --teal: #3fc1b5;
    --navy: #322e58;
    --navy-deep: #2a2650;
    --yellow: #ffc700;
    --pink: #ff0069;
    --green: #93db40;
    --white: #ffffff;
    --pencil-wood: #f4c770;
  }
  * { box-sizing: border-box; margin: 0; padding: 0; }
  html, body { width: 855px; height: 1200px; overflow: hidden; background: var(--navy); }
  .backdrop {
    position: relative;
    width: 855px;
    height: 1200px;
    overflow: hidden;
    background: var(--navy);
    font-family: "Fredoka", "Arial Rounded MT Bold", sans-serif;
  }
  .sky-shape { position: absolute; inset: 0; }
  .brand {
    position: absolute;
    top: 40px; left: 0; width: 100%;
    text-align: center;
    color: var(--white);
    font-weight: 700;
    font-size: 38px;
    letter-spacing: 1px;
  }
  .pencil-art {
    position: absolute;
    left: 285px; top: 130px;
    width: 390px; height: 60px;
    border-radius: 8px;
    background: linear-gradient(90deg, var(--pencil-wood) 0%, var(--yellow) 20%, #ffb400 80%, var(--pink) 100%);
  }
  .headline {
    position: absolute;
    top: 250px; left: 0; width: 100%;
    text-align: center;
    font-family: "Luckiest Guy", "Impact", sans-serif;
    color: var(--white);
    font-size: 104px;
    line-height: 0.98;
    letter-spacing: 2px;
    text-shadow: 5px 6px 0 var(--navy);
  }
  .tagline {
    position: absolute;
    top: 485px; left: 0; width: 100%;
    text-align: center;
    font-family: "Luckiest Guy", "Impact", sans-serif;
    color: var(--yellow);
    font-size: 48px;
    letter-spacing: 1px;
    text-shadow: 3px 3px 0 var(--navy);
  }
  .backpack-art {
    position: absolute;
    left: 318px; top: 670px;
    width: 220px; height: 270px;
    border-radius: 70px 70px 24px 24px;
    background: linear-gradient(180deg, #4a8fd6 0%, #2f6fb8 100%);
  }
  .promise {
    position: absolute;
    left: 60px; top: 722px;
    width: 250px;
    font-family: "Luckiest Guy", "Impact", sans-serif;
    color: var(--yellow);
    font-size: 36px;
    line-height: 1.1;
    letter-spacing: 1px;
  }
  .age-badge {
    position: absolute;
    left: 583px; top: 695px;
    width: 190px; height: 190px;
    border-radius: 50%;
    background: var(--pink);
    color: var(--white);
    display: flex; align-items: center; justify-content: center;
    text-align: center;
    font-family: "Luckiest Guy", "Impact", sans-serif;
    font-size: 22px;
    line-height: 1.2;
    letter-spacing: 0.5px;
    padding: 20px;
  }
  .footer {
    position: absolute;
    top: 992px; left: 0; width: 100%;
    text-align: center;
  }
  .services {
    color: var(--teal);
    font-weight: 600;
    font-size: 19px;
    letter-spacing: 0.5px;
  }
  .motto {
    font-family: "Luckiest Guy", "Impact", sans-serif;
    color: var(--yellow);
    font-size: 34px;
    letter-spacing: 1px;
    margin-top: 8px;
  }
  .motto-sub {
    font-family: "Luckiest Guy", "Impact", sans-serif;
    color: var(--teal);
    font-size: 28px;
    letter-spacing: 1px;
    margin-top: 2px;
  }
  .web {
    color: var(--white);
    font-weight: 600;
    font-size: 18px;
    margin-top: 8px;
  }
  .stationery-left {
    position: absolute;
    left: 0; top: 930px;
    width: 115px; height: 270px;
    border-top-right-radius: 40px;
    background: linear-gradient(160deg, #e8433f 0%, var(--yellow) 55%, #d65a3a 100%);
  }
  .stationery-right {
    position: absolute;
    right: 0; top: 985px;
    width: 100px; height: 215px;
    border-top-left-radius: 24px;
    background: linear-gradient(200deg, #f29a2e 0%, #f1b23c 60%, #e07f22 100%);
  }
</style>
</head>
<body>
  <main class="backdrop">
    <svg class="sky-shape" width="855" height="1200" viewBox="0 0 855 1200" aria-hidden="true">
      <path fill="var(--teal)" d="M0,0 H855 V565 C820,600 760,560 700,600 C620,650 545,610 515,655 L505,690 H350 L340,655 C310,610 235,650 155,600 C95,562 40,605 0,575 Z"/>
    </svg>

    <div class="brand">Pen Path Learning</div>
    <div class="pencil-art" role="img" aria-label="Illustration of a yellow pencil lying horizontally"></div>

    <h1 class="headline">Believe in<br>yourself</h1>
    <p class="tagline">Make it happen</p>

    <div class="backpack-art" role="img" aria-label="Illustration of a blue school backpack"></div>

    <p class="promise">Make it<br>readble<br>in 66 days</p>

    <div class="age-badge">Handwritting<br>lessons<br>6–16 years</div>

    <footer class="footer">
      <p class="services">EXAM READY HANDWRITTING - COURSES - ONLINE LESSONS</p>
      <p class="motto">You can never have enough</p>
      <p class="motto-sub">Parkour skills</p>
      <p class="web">www.penpathlearning.co.uk</p>
    </footer>

    <div class="stationery-left" role="img" aria-label="Illustration of coloured pencils and a ruler"></div>
    <div class="stationery-right" role="img" aria-label="Illustration of an orange notebook"></div>
  </main>
</body>
</html>
```